Logo for a Food & Beverage Franchise Company

We need a logo and stationary for a new company that just aquired a restaurant franchise. We need a sleep and professional logo with stationary.

Target Market(s)

Adults, resturaunt owners, franchisors (Companies who own food franchise companies such as Farrowbys Head Office, Toastwell International Franchise)
and Big Food and Beverage who wish to give franchise rights to us)

Industry/Entity Type

Restaurant

Logo Text

Velvet Harbor

Logo styles of interest
Emblem Logo
Pictorial/Combination Logo
Character Logo
Font styles to use
Serif
Sans Serif

Colors
ffc214
f78f20
f37022
faa54b
fece3e
fbed22

Requirements
Must have
• Maximum three color. The less the better.
Nice to have
• It does not have to have a crown, but if you wish to have a crown then it does not have to be so sharp and clear. Abstract is better.

```html
<!DOCTYPE html>
<html lang="en">
<head>
<meta charset="utf-8">
<title>Velvet Harbor – Business Cards</title>
<link href="https://fonts.googleapis.com/css2?family=Source+Sans+3:wght@400;600&display=swap" rel="stylesheet">
<style>
  :root {
    --backdrop: #ececec;
    --card-orange: #fa9e0c;
    --card-white: #ffffff;
    --card-shadow: rgba(0, 0, 0, 0.18);
  }
  * { box-sizing: border-box; margin: 0; padding: 0; }
  html, body {
    width: 1200px;
    height: 800px;
    overflow: hidden;
    background: var(--backdrop);
    font-family: "Source Sans 3", Arial, sans-serif;
  }
  .stationery {
    position: relative;
    width: 1200px;
    height: 800px;
  }
  .card {
    position: absolute;
    width: 525px;
    height: 300px;
    background: var(--card-orange);
    color: var(--card-white);
    box-shadow: 0 6px 14px var(--card-shadow);
    overflow: hidden;
  }
  .card--front {
    left: 110px;
    top: 90px;
  }
  .card--back {
    left: 565px;
    top: 410px;
  }
  .front-wordmark {
    position: absolute;
    inset: 0;
    display: flex;
    align-items: center;
    justify-content: center;
    font-weight: 600;
    font-size: 34px;
    letter-spacing: 0.22em;
    text-transform: uppercase;
  }
  .back-wordmark {
    position: absolute;
    top: 86px;
    left: 0;
    right: 0;
    text-align: center;
    font-weight: 600;
    font-size: 17px;
    letter-spacing: 0.28em;
    text-transform: uppercase;
  }
  .contact {
    position: absolute;
    left: 42px;
    bottom: 34px;
    font-weight: 600;
    font-size: 15px;
    line-height: 1.3;
  }
  .contact__person { margin-bottom: 14px; }
</style>
</head>
<body>
  <main class="stationery">
    <section class="card card--front" aria-label="Business card front">
      <div class="front-wordmark">Velvet Harbor</div>
    </section>

    <section class="card card--back" aria-label="Business card back">
      <div class="back-wordmark">Velvet Harbor</div>
      <div class="contact">
        <div class="contact__person">
          <p class="contact__name">Rami Al Qasim</p>
          <p class="contact__title">C.E.O.</p>
        </div>
        <p class="contact__line">Office: +9714 418 2093</p>
        <p class="contact__line">Mobile: +97150 627 4185</p>
        <p class="contact__line">Email: rami@velvetharbor.com</p>
        <p class="contact__line">P.O. Box 5210, Dubai, UAE</p>
      </div>
    </section>
  </main>
</body>
</html>
```